fernwick study hub community

The website presents a new interactive learning system where it provides not only the teaching material as the instructor friend who can both teach and learn, making friends and making money.
Make friends and get money.

```html
<!DOCTYPE html>
<html lang="en">
<head>
<meta charset="utf-8">
<title>Fernwick Study Hub</title>
<link href="https://fonts.googleapis.com/css2?family=Raleway:wght@400;600;700;800&family=Open+Sans:wght@400;600&display=swap" rel="stylesheet">
<style>
:root{
  --blue:#1e88d6;
  --blue-dark:#1672b8;
  --ink:#3a3a3a;
  --muted:#7a7a7a;
  --dark:#101820;
  --footer:#0c1219;
  --white:#ffffff;
  --hero-a:#c9b49a;
  --hero-b:#7c6a5a;
  --band-a:#6d6257;
  --band-b:#b9a58f;
}
*{margin:0;padding:0;box-sizing:border-box}
html,body{width:814px;height:1200px;overflow:hidden;background:var(--white)}
body{font-family:"Open Sans",Arial,sans-serif;color:var(--ink);position:relative}

.hero{position:absolute;left:0;top:0;width:814px;height:385px;
  background:linear-gradient(120deg,var(--hero-b) 0%,var(--hero-a) 45%,#e4d7c6 70%,var(--hero-b) 100%)}
.site-header{position:absolute;left:0;top:0;width:814px;height:44px;background:rgba(10,16,24,.88);display:flex;align-items:center;justify-content:space-between;padding:0 30px 0 18px}
.brand{display:flex;align-items:center;gap:7px;color:var(--white);font-family:"Raleway",sans-serif;font-weight:800;font-size:17px;letter-spacing:1px;text-transform:uppercase}
.brand-dot{width:8px;height:8px;border-radius:50%;background:var(--blue)}
.main-nav{display:flex;gap:30px;font-family:"Raleway",sans-serif;font-size:9.5px;font-weight:600;letter-spacing:.5px;color:var(--white);text-transform:uppercase}
.main-nav .active{color:var(--blue)}
.hero-card{position:absolute;left:46px;top:168px;width:290px;background:rgba(20,26,32,.78);padding:18px 20px 16px}
.hero-card h1{font-family:"Raleway",sans-serif;font-weight:800;color:var(--white);font-size:19px;line-height:1.25;text-transform:uppercase}
.hero-card p{color:#d8d8d8;font-size:8.5px;line-height:1.5;margin-top:8px}

.how{position:absolute;top:385px;left:0;width:814px;height:345px;text-align:center}
.section-title{font-family:"Raleway",sans-serif;font-weight:800;color:var(--blue);font-size:20px;text-transform:uppercase;letter-spacing:.5px}
.how .section-title{margin-top:42px}
.steps{display:flex;justify-content:space-between;width:620px;margin:28px auto 0}
.step{width:170px}
.step svg{display:block;margin:0 auto}
.step h3{font-family:"Open Sans",sans-serif;font-weight:400;font-size:15px;margin-top:16px;color:var(--ink)}
.step p{font-size:8.5px;color:var(--muted);line-height:1.55;margin-top:8px}

.quote-band{position:absolute;top:730px;left:0;width:814px;height:132px;background:linear-gradient(90deg,var(--band-a) 0%,#8a7c6d 40%,var(--band-b) 100%)}
.quote-band::after{content:"";position:absolute;inset:0;background:rgba(30,30,30,.45)}
.quote-body{position:absolute;z-index:1;left:95px;top:30px;width:470px;color:var(--white)}
.quote-mark{position:absolute;left:-52px;top:-12px;font-family:"Raleway",sans-serif;font-weight:800;font-size:52px;line-height:1;color:var(--white)}
.quote-body p{font-size:8.5px;line-height:1.6}
.quote-body .read{display:block;text-align:center;margin-top:10px;font-size:8px}

.info{position:absolute;top:862px;left:0;width:814px;height:278px;display:flex;padding:0 42px;justify-content:space-between}
.about{width:370px}
.info .section-title{margin-top:36px;font-size:20px}
.about p{font-size:8.5px;line-height:1.6;color:var(--muted);margin-top:12px}
.about p+p{margin-top:8px}
.btn{display:inline-block;background:var(--blue);color:var(--white);font-size:9px;padding:8px 14px;border-radius:2px;margin-top:14px}
.what{width:300px}
.what-list{list-style:none;margin-top:18px}
.what-list li{display:flex;align-items:center;justify-content:space-between;background:var(--blue);color:var(--white);font-size:8.5px;padding:0 8px 0 10px;height:24px;border-radius:2px;margin-bottom:8px}
.what-list li.short{width:150px}
.arrow-dot{width:14px;height:14px;border-radius:50%;background:var(--white);display:flex;align-items:center;justify-content:center}

.site-footer{position:absolute;left:0;top:1140px;width:814px;height:60px;background:var(--footer);padding:14px 30px 0 42px}
.foot-nav{display:flex;gap:36px;font-family:"Raleway",sans-serif;font-weight:600;font-size:8.5px;color:var(--white);text-transform:uppercase}
.foot-nav .active{color:var(--blue)}
.copyright{font-size:8px;color:#9aa3ad;margin-top:8px}
.social{position:absolute;right:30px;top:16px;display:flex;gap:6px;align-items:center}
.social span{width:26px;height:26px;border-radius:2px}
.s1{background:#3b5998}.s2{background:#29a9e1}.s3{background:#f29423}.s4{background:#d9352b}
.social .up{width:auto;height:auto;color:#9aa3ad;font-size:8px;margin-left:6px}
</style>
</head>
<body>

<section class="hero" role="img" aria-label="Photo of smiling students studying together with books and a laptop">
  <header class="site-header">
    <div class="brand"><span class="brand-dot"></span>Fernwick</div>
    <nav class="main-nav">
      <span class="active">Home</span><span>About Us</span><span>How It Works</span><span>What We Do</span><span>Contact Us</span>
    </nav>
  </header>
  <div class="hero-card">
    <h1>By making<br>friends you can make money</h1>
    <p>Join a study circle where you teach what you know, learn what you need and earn as you go with friends.</p>
  </div>
</section>

<section class="how">
  <h2 class="section-title">How it works</h2>
  <div class="steps">
    <div class="step">
      <svg width="46" height="68" viewBox="0 0 46 68"><path d="M23 0 C30 18 46 34 46 45 A23 23 0 0 1 0 45 C0 34 16 18 23 0Z" fill="var(--blue)"/></svg>
      <h3>Lorem Ipsum is simply</h3>
      <p>Sed ut perspiciatis unde omnis iste natus error sit voluptatem accusantium dolor.</p>
    </div>
    <div class="step">
      <svg width="46" height="68" viewBox="0 0 46 68"><path d="M23 0 C30 18 46 34 46 45 A23 23 0 0 1 0 45 C0 34 16 18 23 0Z" fill="var(--blue)"/></svg>
      <h3>Lorem Ipsum is simply</h3>
      <p>Sed ut perspiciatis unde omnis iste natus error sit voluptatem accusantium dolor.</p>
    </div>
    <div class="step">
      <svg width="46" height="68" viewBox="0 0 46 68"><path d="M23 0 C30 18 46 34 46 45 A23 23 0 0 1 0 45 C0 34 16 18 23 0Z" fill="var(--blue)"/></svg>
      <h3>Lorem Ipsum is simply</h3>
      <p>Sed ut perspiciatis unde omnis iste natus error sit voluptatem accusantium dolor.</p>
    </div>
  </div>
</section>

<section class="quote-band" role="img" aria-label="Photo of a student working at a laptop">
  <div class="quote-body">
    <span class="quote-mark">&ldquo;</span>
    <p>Sed ut perspiciatis unde omnis iste natus error sit voluptatem accusantium doloremque laudantium, totam rem aperiam, eaque ipsa quae ab illo inventore veritatis et quasi architecto beatae vitae dicta sunt explicabo.</p>
    <span class="read">Read more about us</span>
  </div>
</section>

<section class="info">
  <div class="about">
    <h2 class="section-title">About us</h2>
    <p>Lorem ipsum dolor sit amet, consectetur adipiscing elit. Suspendisse viverra mauris eget tortor imperdiet vehicula. Proin egestas diam ac mauris molestie hendrerit. Quisque nec nisl tortor. Etiam at mauris et est magna suscipit lacus.</p>
    <p>Sed ut perspiciatis unde omnis iste natus error sit voluptatem accusantium doloremque laudantium, totam rem aperiam, eaque ipsa quae ab illo inventore veritatis et quasi architecto beatae vitae dicta sunt.</p>
    <span class="btn">Read More</span>
  </div>
  <div class="what">
    <h2 class="section-title">What we do</h2>
    <ul class="what-list">
      <li>Lorem ipsum dolor sit amet, consectetur adipiscing elit<span class="arrow-dot"><svg width="6" height="8" viewBox="0 0 6 8"><path d="M1 0 L6 4 L1 8Z" fill="var(--blue)"/></svg></span></li>
      <li>Sed do eiusmod tempor incididunt ut labore<span class="arrow-dot"><svg width="6" height="8" viewBox="0 0 6 8"><path d="M1 0 L6 4 L1 8Z" fill="var(--blue)"/></svg></span></li>
      <li class="short">Capacity Planning<span class="arrow-dot"><svg width="6" height="8" viewBox="0 0 6 8"><path d="M1 0 L6 4 L1 8Z" fill="var(--blue)"/></svg></span></li>
    </ul>
  </div>
</section>

<footer class="site-footer">
  <nav class="foot-nav">
    <span class="active">Home</span><span>About Us</span><span>How It Works</span><span>What We Do</span><span>Contact Us</span>
  </nav>
  <p class="copyright">&copy; 2014 Fernwick. All rights reserved.</p>
  <div class="social">
    <span class="s1"></span><span class="s2"></span><span class="s3"></span><span class="s4"></span><span class="up">Up</span>
  </div>
</footer>

</body>
</html>
```